Label design needed for a new brain focus supplement. Velmarix.com

Hi I’m looking for a quality label design for a my new supplement. The supplement is a nootropic (brain focus booster). I’ll also upload my competitors designs as a reference and to get some ideas.

I was thinking to use a white glossy background with the gold logo in top with some gold graphics added. Along with some focus driven text.

Dimensions for label are 300mm x 105mm Landscape. Please allow a 5mm safe text area.

Target Market(s)

High achieving focus driven People.

Font styles to use
Sans Serif

Colors

Designer to choose colors to be used in the design.

Requirements
Must have
• Good quality design.
Nice to have
• wording to use on label
• ULTRA CLARITY
• Brain food supplement
• High quality
• Premium blend
• Dietary supplement
Should not have
• Bright colourful colours. This is a premium product and label should show this

```html
<!DOCTYPE html>
<html lang="en">
<head>
<meta charset="utf-8">
<title>Velmarix Ultra Clarity – Label</title>
<link rel="stylesheet" href="https://fonts.googleapis.com/css2?family=Fira+Sans+Condensed:wght@800&family=Ubuntu:wght@400;500;700&display=swap">
<style>
  :root {
    --canvas: #eeeeee;
    --label-light: #f7f8f9;
    --label-mid: #dfe2e5;
    --label-shade: #cfd3d7;
    --gold: #b88f22;
    --gold-pale: #f4eeb4;
    --gold-deep: #c2861f;
    --ink: #141414;
    --ink-soft: #3a3a3a;
    --rule: #555555;
    --blue: #2fa8de;
    --orange: #e88a1c;
    --green: #5aa637;
    --white: #ffffff;
  }
  * { margin: 0; padding: 0; box-sizing: border-box; }
  html, body {
    width: 1200px; height: 800px; overflow: hidden;
    background: var(--canvas);
    font-family: "Ubuntu", sans-serif;
  }
  .label {
    position: absolute; left: 210px; top: 5px;
    width: 780px; height: 790px;
    background: linear-gradient(90deg, var(--label-mid) 0%, var(--label-light) 30%, var(--label-shade) 55%, var(--label-light) 80%, var(--label-mid) 100%);
    overflow: hidden;
  }
  .brand {
    position: absolute; top: 52px; left: 0; width: 100%;
    text-align: center;
    color: var(--gold); font-weight: 500; font-size: 58px; line-height: 1;
  }
  .product-name {
    position: absolute; top: 142px; left: 0; width: 100%;
    text-align: center;
    font-family: "Fira Sans Condensed", sans-serif; font-weight: 800;
    font-size: 78px; line-height: 1; color: var(--ink); letter-spacing: -1px;
  }
  .product-name .accent { color: var(--ink-soft); }
  .tagline {
    position: absolute; top: 218px; left: 0; width: 100%;
    text-align: center; padding-left: 60px;
    font-size: 24px; letter-spacing: 2.5px; color: var(--ink);
  }
  .hero-art {
    position: absolute; left: 202px; top: 282px;
    width: 357px; height: 254px; border-radius: 120px 120px 110px 110px;
    background: radial-gradient(ellipse at 50% 55%, #e6c45a 0%, #c79a2b 55%, #9c7418 100%);
  }
  .benefit-box {
    position: absolute; left: 136px; top: 580px;
    width: 499px; height: 97px;
    border: 1.5px solid var(--rule); border-bottom: none;
    border-radius: 12px 12px 0 0;
  }
  .benefit-pill {
    position: absolute; left: 50%; top: -14px; transform: translateX(-50%);
    background: var(--ink); color: var(--white);
    font-size: 17px; font-weight: 500; letter-spacing: 4px;
    padding: 4px 12px 4px 16px; border-radius: 14px;
  }
  .benefits {
    position: absolute; left: 16px; right: 16px; top: 34px;
    display: flex; justify-content: space-between; align-items: center;
  }
  .benefit { display: flex; align-items: center; gap: 7px; font-size: 20px; color: var(--ink); white-space: nowrap; }
  .benefit svg { width: 34px; height: 34px; flex: none; }
  .category {
    position: absolute; left: 136px; top: 666px; width: 499px; height: 22px;
    display: flex; align-items: center; gap: 6px;
    font-size: 17px; line-height: 22px; color: var(--ink); letter-spacing: 0.5px;
  }
  .category::before, .category::after { content: ""; flex: 1; height: 1.5px; background: var(--rule); }
  .quality {
    position: absolute; top: 720px; left: 0; width: 100%;
    text-align: center; font-size: 14px; font-weight: 700; letter-spacing: 2.5px; color: var(--ink);
  }
  .gold-band {
    position: absolute; left: 0; top: 750px; width: 100%; height: 22px;
    background: linear-gradient(90deg, var(--gold-pale) 0%, #eadf9a 35%, #c9a64a 70%, var(--gold-deep) 100%);
  }
  .label-foot {
    position: absolute; left: 0; top: 772px; width: 100%; height: 18px; background: var(--white);
  }
</style>
</head>
<body>
  <main class="label">
    <div class="brand">Velmarix</div>
    <h1 class="product-name">ULTRA <span class="accent">CLARITY</span></h1>
    <p class="tagline">Brain food supplement</p>
    <div class="hero-art" role="img" aria-label="Gold brain illustration with flexing muscular arms"></div>

    <section class="benefit-box">
      <span class="benefit-pill">NOOTROPIC</span>
      <div class="benefits">
        <div class="benefit">
          <svg viewBox="0 0 34 34"><circle cx="17" cy="17" r="17" fill="var(--blue)"/><circle cx="17" cy="13" r="5" fill="none" stroke="#fff" stroke-width="2"/><path d="M10 26c1-5 13-5 14 0z" fill="#fff"/></svg>
          MOTIVATION
        </div>
        <div class="benefit">
          <svg viewBox="0 0 34 34"><circle cx="17" cy="17" r="17" fill="var(--orange)"/><circle cx="17" cy="17" r="9" fill="none" stroke="#fff" stroke-width="2"/><path d="M18 10l-5 8h4l-1 6 5-8h-4z" fill="#fff"/></svg>
          ENERGY
        </div>
        <div class="benefit">
          <svg viewBox="0 0 34 34"><circle cx="17" cy="17" r="17" fill="var(--green)"/><rect x="9" y="21" width="3" height="5" fill="#fff"/><rect x="14" y="18" width="3" height="8" fill="#fff"/><rect x="19" y="15" width="3" height="11" fill="#fff"/><path d="M10 16l8-7m0 0h-4m4 0v4" stroke="#fff" stroke-width="2" fill="none"/></svg>
          PERFORMANCE
        </div>
      </div>
    </section>
    <p class="category">DIETARY SUPPLEMENT</p>

    <p class="quality">● HIGH QUALITY ● PREMIUM BLEND</p>
    <div class="gold-band"></div>
    <div class="label-foot"></div>
  </main>
</body>
</html>
```